Business Card Design Competition

We need a business card design for our Internet Marketing company. We require both front and back designs and the final card must be 89x53mm in size, plus crop marks to 91x55mm. Colours as per logo, plus perhaps black and/or grey (#828282).
Final text must be editable (if you can supply an editable Fireworks PNG, even better)...
FRONT TEXT:
Full Name
Position
Address Line
Suburb, State, Postcode
Phone: 0000 000 000
Mobile: 0000 000 000
Email: xxx@brightlanemedia.com.au
Web: www.brightlanemedia.com.au
Rear of card should be a fresh design plus our slogan text: "Helping You Stand Out" in large font, then in small text "Kestrel Holdings Pty Ltd (ABN: 42 561 903 774)".
Target Market(s)
Small/Medium Businesses
Industry/Entity Type
Business

```html
<!DOCTYPE html>
<html lang="en">
<head>
<meta charset="utf-8">
<title>Brightlane Media – Business Cards</title>
<link rel="stylesheet" href="https://fonts.googleapis.com/css2?family=Source+Sans+3:wght@400;600;700&display=swap">
<style>
  :root {
    --backdrop: #e4e4e2;
    --charcoal: #2a2a2a;
    --charcoal-deep: #1f1f1f;
    --lime: #8cc63f;
    --orange: #f7a21b;
    --white: #ffffff;
    --paper-top: #ffffff;
    --paper-bottom: #e6e6e6;
    --grey: #828282;
  }
  * { margin: 0; padding: 0; box-sizing: border-box; }
  html, body { width: 1200px; height: 900px; overflow: hidden; }
  body {
    position: relative;
    background: var(--backdrop);
    font-family: "Source Sans 3", "Helvetica Neue", Arial, sans-serif;
  }
  .card {
    position: absolute;
    top: 290px;
    width: 546px;
    height: 312px;
    border-radius: 14px;
    overflow: hidden;
    box-shadow: 0 4px 14px rgba(0,0,0,0.25);
  }
  /* Front */
  .card-front { left: 36px; background: var(--charcoal); }
  .front-header {
    position: absolute; left: 0; top: 0; width: 100%; height: 134px;
    background: linear-gradient(180deg, var(--paper-top) 0%, var(--paper-bottom) 100%);
  }
  .front-rule {
    position: absolute; left: 0; top: 134px; width: 100%; height: 9px;
    background: var(--lime);
  }
  .brand {
    position: absolute; left: 0; right: 0; top: 42px;
    display: flex; justify-content: center; align-items: center; gap: 14px;
  }
  .brand-dot {
    width: 46px; height: 46px; border-radius: 50%;
    background: var(--lime);
  }
  .brand-name {
    font-size: 36px; font-weight: 600; color: var(--lime);
    letter-spacing: 0.5px;
  }
  .holder { position: absolute; left: 47px; top: 202px; }
  .holder-name { font-size: 23px; font-weight: 700; color: var(--lime); line-height: 1.1; }
  .holder-role { font-size: 16px; color: var(--white); line-height: 1.2; }
  .contact {
    position: absolute; left: 306px; top: 160px;
    color: var(--white); font-size: 12.5px; line-height: 17px;
  }
  .contact-address { margin-bottom: 12px; }
  .contact-row { display: flex; align-items: center; gap: 8px; }
  .contact-row svg { width: 12px; height: 12px; flex: none; }
  .contact-group { margin-bottom: 12px; }
  /* Back */
  .card-back {
    left: 621px;
    background: linear-gradient(135deg, var(--charcoal) 0%, var(--charcoal-deep) 100%);
  }
  .back-disc {
    position: absolute; left: 390px; top: 12px;
    width: 290px; height: 290px; border-radius: 50%;
    background: var(--lime);
  }
  .back-brand {
    position: absolute; left: 46px; top: 104px;
    font-size: 38px; font-weight: 600; color: var(--orange);
    line-height: 1.0; letter-spacing: 0.5px;
  }
  .slogan {
    position: absolute; left: 46px; top: 186px;
    font-size: 21px; color: var(--white);
  }
  .legal {
    position: absolute; left: 24px; top: 284px;
    font-size: 12px; color: var(--white);
  }
</style>
</head>
<body>

<section class="card card-front" aria-label="Business card front">
  <div class="front-header"></div>
  <div class="front-rule"></div>
  <div class="brand">
    <span class="brand-dot"></span>
    <span class="brand-name">Brightlane Media</span>
  </div>

  <div class="holder">
    <p class="holder-name">Liam Porter</p>
    <p class="holder-role">Company Director</p>
  </div>

  <div class="contact">
    <p class="contact-address">18 Harbour View Road, Millbrook<br>County Ardlow BT31 4QX 5678</p>
    <div class="contact-group">
      <p class="contact-row">
        <svg viewBox="0 0 12 12" aria-hidden="true"><rect x="3" y="0.5" width="6" height="11" rx="1.2" fill="var(--orange)"/><rect x="4" y="2" width="4" height="6" fill="var(--charcoal)"/></svg>
        061-555-0142
      </p>
      <p class="contact-row">
        <svg viewBox="0 0 12 12" aria-hidden="true"><path d="M1 4 Q6 0 11 4 L10 6 L8 5 L8 4 Q6 3 4 4 L4 5 L2 6 Z" fill="var(--orange)"/><rect x="2" y="6.5" width="8" height="4.5" rx="1" fill="var(--orange)"/></svg>
        061-555-0187
      </p>
    </div>
    <p class="contact-row">
      <svg viewBox="0 0 12 12" aria-hidden="true"><rect x="0.8" y="2.5" width="10.4" height="7" fill="none" stroke="var(--orange)" stroke-width="1.3"/><path d="M1 3 L6 7 L11 3" fill="none" stroke="var(--orange)" stroke-width="1.2"/></svg>
      liam@brightlanemedia.com.au
    </p>
    <p class="contact-row">
      <svg viewBox="0 0 12 12" aria-hidden="true"><circle cx="6" cy="6" r="5" fill="none" stroke="var(--orange)" stroke-width="1.3"/><ellipse cx="6" cy="6" rx="2.2" ry="5" fill="none" stroke="var(--orange)" stroke-width="1"/><line x1="1" y1="6" x2="11" y2="6" stroke="var(--orange)" stroke-width="1"/></svg>
      brightlanemedia.com.au
    </p>
  </div>
</section>

<section class="card card-back" aria-label="Business card back">
  <div class="back-disc"></div>
  <p class="back-brand">Brightlane<br>Media</p>
  <p class="slogan">Helping You Stand Out</p>
  <p class="legal">Kestrel Holdings Pty Ltd (ABN: 42 561 903 774)</p>
</section>

</body>
</html>
```